Tall Fern Roofing Business Card

Need a business card with the logo that was designed here

Contact Information for Business Card

Name, Title, Phone, Email, Website, Company name

```html
<!DOCTYPE html>
<html lang="en">
<head>
<meta charset="utf-8">
<title>Tall Fern Roofing Business Card</title>
<link href="https://fonts.googleapis.com/css2?family=Poppins:wght@400;600&display=swap" rel="stylesheet">
<style>
  :root {
    --backdrop: #e3e4e6;
    --card: #ffffff;
    --brand-blue: #1e73be;
    --brand-grey: #8a8b8d;
    --ink: #1d1d1f;
    --shadow: rgba(0, 0, 0, 0.35);
  }
  * { margin: 0; padding: 0; box-sizing: border-box; }
  html, body {
    width: 1200px;
    height: 900px;
    overflow: hidden;
    background: var(--backdrop);
    font-family: "Poppins", sans-serif;
  }
  .stage { position: relative; width: 1200px; height: 900px; }
  .card {
    position: absolute;
    top: 217px;
    width: 308px;
    height: 499px;
    background: var(--card);
    box-shadow: 2px 3px 4px var(--shadow);
  }
  .card--front { left: 279px; border-radius: 0 54px 0 54px; }
  .card--back { left: 617px; border-radius: 54px 0 54px 0; }

  .wordmark {
    position: absolute;
    left: 0;
    right: 0;
    display: flex;
    align-items: center;
    justify-content: center;
    gap: 8px;
    color: var(--brand-blue);
    font-weight: 600;
    font-size: 25px;
    white-space: nowrap;
  }
  .wordmark__square { width: 14px; height: 14px; background: var(--brand-blue); }
  .card--front .wordmark { top: 236px; }
  .card--back .wordmark { top: 160px; }

  .person { position: absolute; left: 32px; top: 322px; }
  .person__name {
    font-weight: 600;
    font-size: 20px;
    line-height: 1.1;
    color: var(--brand-blue);
    letter-spacing: 0.2px;
  }
  .person__name .surname { color: var(--brand-grey); }
  .person__title { font-size: 14.5px; color: var(--brand-blue); line-height: 1.2; }

  .contacts { position: absolute; left: 32px; top: 374px; list-style: none; }
  .contacts li {
    display: flex;
    align-items: center;
    gap: 5px;
    font-size: 14.5px;
    line-height: 18.5px;
    color: var(--ink);
  }
  .contacts svg { width: 13px; height: 13px; fill: var(--brand-blue); flex: none; }
</style>
</head>
<body>
<main class="stage">
  <section class="card card--front">
    <div class="wordmark"><span class="wordmark__square"></span>Tall Fern Roofing</div>
  </section>

  <section class="card card--back">
    <div class="wordmark"><span class="wordmark__square"></span>Tall Fern Roofing</div>

    <div class="person">
      <p class="person__name">DANIEL <span class="surname">HARPER</span></p>
      <p class="person__title">Managing Director</p>
    </div>

    <ul class="contacts">
      <li>
        <svg viewBox="0 0 24 24" aria-hidden="true"><path d="M6.6 10.8a15.1 15.1 0 0 0 6.6 6.6l2.2-2.2a1 1 0 0 1 1-.25 11.4 11.4 0 0 0 3.6.57 1 1 0 0 1 1 1V20a1 1 0 0 1-1 1A17 17 0 0 1 3 4a1 1 0 0 1 1-1h3.5a1 1 0 0 1 1 1c0 1.25.2 2.46.57 3.6a1 1 0 0 1-.25 1z"/></svg>
        044-555 210 347
      </li>
      <li>
        <svg viewBox="0 0 24 24" aria-hidden="true"><path d="M2 5h20v14H2z M2 5l10 8 10-8" fill="var(--brand-blue)"/><path d="M2 5l10 8 10-8" fill="none" stroke="#fff" stroke-width="1.6"/></svg>
        info@tallfernroofing.com
      </li>
      <li>
        <svg viewBox="0 0 24 24" aria-hidden="true"><circle cx="12" cy="12" r="10"/><path d="M2 12h20M12 2c3 3 3 17 0 20M12 2c-3 3-3 17 0 20M4 7h16M4 17h16" fill="none" stroke="#fff" stroke-width="1.3"/></svg>
        www.tallfernroofing.com
      </li>
    </ul>
  </section>
</main>
</body>
</html>
```